Creative UI design for web application

I need a new UI design for my web application. It will be used by small and micro business owners to plan & implement growth tactics.

I've attached the current design (which I'm open to be changed) - but in particular I need to design the centre of the screen, where the work actually happens.

There needs to be place for a title (YOUR BUSINESS) and description (say 1-2 paragraphs of text) - and am happy to include icons or imagery where makes sense. It may make sense for the user to be able to upload their business logo and name, for example.

This screen will be used by the business owner to understand the real value they offer potential customers and their point of difference - why they exist and why potential customers should care.

They'll use the information they put into this screen to plan things like their messaging.

Following that, there needs to be 2 sections in the dashboard.

The first section is titled "WHO YOU ARE"

The first section will include a number of boxes that the user can input information into, as follows:

- Logo
- Business name
- Business tag line
- Business vision
- Business bio
- Brand colours (these should end up as swatches based on the colour code they enter) - the colour code for each colour swatch should also be visible.
- Key competitors
- SWOT analysis (boxes to enter their strengths, weaknesses, opportunities and threats).

The second section is titled "WHY YOU EXIST"

The second section will include a number of boxes that the user can input information (text) into, as follows:

- Who are your ideal customers?
- What problem are you trying to solve for them?
- What pain points will this remove for them?
- How do you solve it?
- How else could this problem be solved?
- Who offers these other solutions?
- Why is your solution better?
- How much does your solution cost?
- What value are you providing to justify this cost?
- How will this make their life/job easier/better?

They should be able to write a decent amount of information in the boxes.

There should ideally be a place for a description for each of these text fields (for both section 1 & 2) as well so I can give them a little bit more direction around what to put in the box. Alternatively there could be a little icon (say a question mark or "i") that they could click on to view instructions. The instructions will be around 2-4 sentences long for each text field.

You have 2 options:

a) This all needs to appear on the one screen, and the navigation needs to be visible (as per the example attached but feel free to recreate this navigation)

Note: the page can scroll below the fold - but please provide the design for the full length of the page.

b) Potentially the 2 sections could actually be in 2 different items in the menu - YOUR BUSINESS and YOUR VALUE (which would sit next to YOUR BUSINESS and before YOUR CUSTOMER in the screenshot provided). feel free to design them as 2 separate screens if you prefer.

I have attached a screenshot of the app as it stands today (screen shot 2017) which would still exist in the new design but under a different section (the learn section from the plan2 mockup attached)

I have mocked up how this new screen could look if broken into 2 and that's also attached. If you can make this come to life - and look more engaging that would be helpful! :)

Target Market(s)

Small and micro business owners

Industry/Entity Type

Marketing

Number of Pages Required

1 page

Font styles to use
Sans Serif
Other font styles liked:
• Montserrat

Colors
87cfc6
d2a4cc
ffffff
85cae6
e8e8e8
5c5c5c

Requirements
Must have
• Use of my brand colours: #cc8eb2, #76d6c8, #68c7ff as well as white and #595959. Must be visually pleasing / engaging, designed for desktop (as it's a desktop application), really easy to use / navigate.
• Use font Montserrat light & Montserrat Regular or Bold. Mostly should be Montserrat light.
Nice to have
• Would be nice to see how this would look on mobile (as the application is responsive) but this is not mandatory.
Should not have
• Should not look too corporate or dry.

```html
<!DOCTYPE html>
<html lang="en">
<head>
<meta charset="utf-8">
<title>Bloompath – Your Value</title>
<link href="https://fonts.googleapis.com/css2?family=Montserrat:wght@300;400;500;700&display=swap" rel="stylesheet">
<style>
  :root {
    --pink: #cc8eb2;
    --teal: #76d6c8;
    --blue: #68c7ff;
    --charcoal: #595959;
    --panel: #f2f2f4;
    --field: #f8f8fa;
    --field-border: #cfcfd4;
    --text: #5c5c5c;
    --white: #ffffff;
  }
  * { box-sizing: border-box; margin: 0; padding: 0; }
  html, body {
    width: 1200px; height: 1200px; overflow: hidden;
    background: var(--white);
    font-family: "Montserrat", sans-serif;
    color: var(--text);
  }
  .topbar {
    height: 43px; background: var(--charcoal);
    display: flex; align-items: center; position: relative;
  }
  .brand {
    position: absolute; left: 56px; top: 13px;
    display: flex; align-items: center; gap: 6px;
    color: var(--white); font-weight: 400; font-size: 17px; letter-spacing: 0.5px;
  }
  .brand-dot { width: 7px; height: 7px; border-radius: 50%; background: var(--teal); }
  .main-nav { position: absolute; left: 276px; top: 7px; display: flex; align-items: center; }
  .main-nav a {
    color: var(--white); text-decoration: none; font-size: 14px; font-weight: 400;
    height: 28px; line-height: 26px; margin-right: 20px;
  }
  .main-nav a.active {
    color: var(--teal); border: 1px solid var(--teal); border-radius: 14px;
    width: 75px; text-align: center;
  }
  .profile {
    position: absolute; right: 50px; top: 12px;
    color: var(--white); font-size: 15px; display: flex; align-items: center; gap: 9px;
  }
  .tabs {
    position: absolute; left: 48px; top: 70px; height: 47px;
    display: flex; background: var(--blue);
  }
  .tab {
    height: 47px; line-height: 47px; text-align: center;
    color: var(--white); font-size: 14px; font-weight: 400;
    border-right: 1px solid rgba(255,255,255,0.35); position: relative;
  }
  .tab:last-child { border-right: none; }
  .tab.active { background: var(--pink); border-right: none; }
  .tab.active::after {
    content: ""; position: absolute; left: 50%; bottom: -7px; transform: translateX(-50%);
    border-left: 7px solid transparent; border-right: 7px solid transparent;
    border-top: 7px solid var(--pink);
  }
  .panel {
    position: absolute; left: 48px; top: 148px; width: 1110px; height: 912px;
    background: var(--panel); padding: 33px 0 0 40px;
  }
  .section-title {
    color: var(--pink); font-weight: 700; font-size: 20px; letter-spacing: 0.3px;
    width: 989px; padding-bottom: 9px; border-bottom: 1px solid #9a9a9e;
  }
  .questions {
    margin-top: 24px; display: grid;
    grid-template-columns: 470px 470px; column-gap: 50px;
  }
  .question { height: 144px; }
  .question label {
    display: flex; align-items: center; gap: 5px;
    height: 24px; padding-left: 3px;
    font-size: 14px; font-weight: 400; color: var(--text);
  }
  .help {
    width: 22px; height: 22px; border-radius: 50%; background: var(--teal);
    color: var(--white); font-size: 12px; display: inline-flex;
    align-items: center; justify-content: center;
  }
  .question textarea {
    margin-top: 8px; width: 470px; height: 90px; display: block;
    background: var(--field); border: 1px solid var(--field-border); border-radius: 2px;
    font-family: inherit; font-weight: 300; font-size: 13px; padding: 10px; color: var(--text);
  }
  .save {
    position: absolute; left: 879px; top: 822px; width: 151px; height: 44px;
    border: none; border-radius: 22px; background: var(--teal);
    color: var(--white); font-family: inherit; font-weight: 700; font-size: 16px;
  }
</style>
</head>
<body>
  <header class="topbar">
    <div class="brand"><span>BLOOMPATH</span><span class="brand-dot"></span></div>
    <nav class="main-nav">
      <a class="active" href="#">Plan</a>
      <a href="#">Learn</a>
      <a href="#">Remember</a>
    </nav>
    <div class="profile">My Profile
      <svg width="8" height="5" viewBox="0 0 8 5"><path d="M0 0h8L4 5z" fill="#ffffff"/></svg>
    </div>
  </header>

  <nav class="tabs">
    <div class="tab" style="width:156px">Your Business</div>
    <div class="tab active" style="width:124px">Your Value</div>
    <div class="tab" style="width:146px">Your Product</div>
    <div class="tab" style="width:167px">Your Customers</div>
    <div class="tab" style="width:128px">Your Goals</div>
    <div class="tab" style="width:149px">Your Plan</div>
  </nav>

  <main class="panel">
    <h2 class="section-title">WHY YOU EXIST</h2>
    <form class="questions">
      <div class="question"><label>Who are your ideal customers? <span class="help">?</span></label><textarea></textarea></div>
      <div class="question"><label>What problem are you trying to solve for them? <span class="help">?</span></label><textarea></textarea></div>
      <div class="question"><label>What pain points will this remove for them? <span class="help">?</span></label><textarea></textarea></div>
      <div class="question"><label>How do you solve it?<span class="help">?</span></label><textarea></textarea></div>
      <div class="question"><label>How else could this problem be solved? <span class="help">?</span></label><textarea></textarea></div>
      <div class="question"><label>Who offers these other solutions? <span class="help">?</span></label><textarea></textarea></div>
      <div class="question"><label>Why is your solution better? <span class="help">?</span></label><textarea></textarea></div>
      <div class="question"><label>How much does your solution cost? <span class="help">?</span></label><textarea></textarea></div>
      <div class="question"><label>What value are you providing to justify this cost? <span class="help">?</span></label><textarea></textarea></div>
      <div class="question"><label>How will this make their life/job easier/better? <span class="help">?</span></label><textarea></textarea></div>
    </form>
    <button class="save" type="button">Save Changes</button>
  </main>
</body>
</html>
```